Thornbury Building Company - Card Design

I am looking to use the logo designs that you already did for me to develop a business card. I would like the card to have a black background and be double sided. I want white and green logo and text. I have attached an inspiration photo of a look that I like. I would like to use the Vertical Logo attached to take up the full front side of the card. On the back where I have my name and information, I would like to have the horizontal logo or maybe even just the image of the 'A' and trees without the text. I am open, but I am looking for something clean and simple and I want the green to really pop! Additional files can be found under Design #: 58302946

Target Market(s)

Homeowners

Industry/Entity Type

Construction

Contact Information for Business Card

Name: Marcus Thornbury, Title: Project Manager, Phone: 555.274.8136, Email: thornburybuildingcompany@mailvesta.com, address: 487 Larkspur Ln, Marlow Creek, CA 95033, Lic# 2468317

Colors
00AB8E
00BBA5
67D7C9
C6EFE9
E9F9F6

Requirements
Nice to have
• I would like to see the logos that I have already got from ArtLoomHub, though I am open to new ones

```html
<!DOCTYPE html>
<html lang="en">
<head>
<meta charset="utf-8">
<title>Thornbury Building Company – Business Card</title>
<link rel="stylesheet" href="https://fonts.googleapis.com/css2?family=Arimo:wght@400;700&display=swap">
<style>
  :root {
    --page-bg: #2a2d35;
    --card-bg: #1c1c1c;
    --green: #62b846;
    --white: #ffffff;
  }
  * { box-sizing: border-box; margin: 0; padding: 0; }
  html, body {
    width: 1200px; height: 900px; overflow: hidden;
    background: var(--page-bg);
    font-family: "Arimo", Arial, sans-serif;
  }
  .canvas {
    width: 1200px; height: 900px;
    display: flex; flex-direction: column; align-items: center; justify-content: center;
    gap: 40px;
  }
  .card {
    position: relative;
    width: 700px; height: 400px;
    border-radius: 26px;
    background: var(--card-bg);
    overflow: hidden;
    box-shadow: 0 12px 30px rgba(0,0,0,.45);
  }
  .card-front::after {
    content: ""; position: absolute; left: 0; right: 0; bottom: 0;
    height: 14px; background: var(--green);
  }
  .brand {
    position: absolute; left: 46px; top: 128px;
    display: flex; align-items: center; gap: 12px;
  }
  .brand-mark { width: 22px; height: 22px; background: var(--green); flex: none; }
  .brand-name {
    color: var(--white); font-weight: 700; font-size: 20px;
    line-height: 1.2; letter-spacing: .5px; text-transform: uppercase;
    white-space: nowrap;
  }
  .divider {
    position: absolute; left: 328px; top: 108px;
    width: 1.5px; height: 176px; background: var(--green);
  }
  .contact {
    position: absolute; left: 350px; top: 108px; right: 18px;
    color: var(--white);
  }
  .contact-name {
    color: var(--green); font-weight: 700; font-size: 24px;
    text-transform: uppercase; letter-spacing: .3px; white-space: nowrap;
  }
  .contact-title { font-size: 16px; margin-top: 4px; }
  .contact-license { color: var(--green); font-size: 15px; margin-top: 14px; }
  .contact-line {
    display: flex; align-items: center; gap: 8px;
    font-size: 15px; margin-top: 8px; white-space: nowrap;
  }
  .contact-line svg { width: 14px; height: 14px; flex: none; fill: var(--green); }
  .contact-email { font-size: 14px; }
  .pattern-fill {
    position: absolute; inset: 0;
    background: linear-gradient(135deg, #1a1a1a 0%, #2e2e2e 50%, #1a1a1a 100%);
  }
  .back-brand {
    position: absolute; right: 40px; bottom: 34px;
    display: flex; align-items: center; gap: 10px;
  }
</style>
</head>
<body>
<main class="canvas">
  <section class="card card-front" aria-label="Business card front">
    <div class="brand">
      <span class="brand-mark"></span>
      <span class="brand-name">Thornbury<br>Building Company</span>
    </div>
    <div class="divider"></div>
    <div class="contact">
      <p class="contact-name">Marcus Thornbury</p>
      <p class="contact-title">Project Manager</p>
      <p class="contact-license">Lic# 2468317</p>
      <p class="contact-line">487 Larkspur Ln, Marlow Creek, CA 95033</p>
      <p class="contact-line">
        <svg viewBox="0 0 24 24" aria-hidden="true"><path d="M6.6 10.8a15.1 15.1 0 0 0 6.6 6.6l2.2-2.2c.3-.3.7-.4 1-.2 1.1.4 2.3.6 3.6.6.6 0 1 .4 1 1V20c0 .6-.4 1-1 1A17 17 0 0 1 3 4c0-.6.4-1 1-1h3.5c.6 0 1 .4 1 1 0 1.3.2 2.5.6 3.6.1.3 0 .7-.2 1z"/></svg>
        555.274.8136
      </p>
      <p class="contact-line contact-email">
        <svg viewBox="0 0 24 24" aria-hidden="true"><path d="M2 5h20v14H2z"/><path d="M2 5l10 8 10-8" fill="none" stroke="#1c1c1c" stroke-width="2"/></svg>
        thornburybuildingcompany@mailvesta.com
      </p>
    </div>
  </section>

  <section class="card card-back" aria-label="Business card back">
    <div class="pattern-fill" role="img" aria-label="Repeating tone-on-tone brand pattern in dark greys"></div>
    <div class="back-brand">
      <span class="brand-mark"></span>
      <span class="brand-name">Thornbury</span>
    </div>
  </section>
</main>
</body>
</html>
```